Brackwell Exteriors Needs a New Website!

We are an exteriors company specializing in vinyl siding, Corwin Maddox siding, aluminum soffit/fascia, trough. We do new construction work as well as renovations. We also build detached garages.
You can view our current website at www.brackwellfabricators.ca
I want to completely overhaul the website.
Our services are different now as we no longer do new home construction as well as we do not do the snow clearing.
I want to focus on 2 things in particular on the website:

1/ Exterior renovations

2/ Detached Garage construction.

I have included our logo in the attached files to use as well.

Some features we would like:

1/ Be able to easily attach a video from Clipverse/Reelio to highlight a product or service
2/ Quick chat or contact button that we can talk to a potential client quickly
3/ Meet the Team page that is interesting and fresh
4/ Place for us to put in helpful exterior tips/suggestions for homeowners.

Content is not important, but looking for the best design that will attract people once they click on our page and want to renovate with us.

Target Market(s)

People looking for renovations on their home, people looking to build a detached garage.

Industry/Entity Type

Residential Construction

Number of Pages Required

5+ page

Font styles to use
Sans Serif

Requirements
Must have
• Fresh and exciting home page.

Simple design. Don't want it over complicated or too much information to confuse the potential client.

Easy way to contact us.

Meet the team page that instills confidence
Nice to have
• Colour of website to go off our logo. Doesn't need to be an exact match, but something that goes well with our blue and grey.

```html
<!DOCTYPE html>
<html lang="en">
<head>
<meta charset="utf-8">
<title>Brackwell Exteriors</title>
<link href="https://fonts.googleapis.com/css2?family=Roboto:wght@400;500;700&display=swap" rel="stylesheet">
<style>
:root{
  --blue:#1559b0;
  --blue-deep:#0f4d9e;
  --ink:#2a2a2a;
  --text:#555;
  --muted:#888;
  --grey-bg:#ebebeb;
  --white:#fff;
  --footer:#2b2b2b;
  --arrow-seg:#555;
}
*{margin:0;padding:0;box-sizing:border-box}
html,body{width:1200px;height:4608px;overflow:hidden}
body{font-family:'Roboto',Arial,sans-serif;color:var(--ink);background:var(--white);position:relative}
.abs{position:absolute}
.section{position:absolute;left:0;width:1200px}
.title{position:absolute;left:0;width:1200px;text-align:center;font-size:32px;font-weight:500;color:#3a3a3a;letter-spacing:.3px}
.title b{color:var(--blue);font-weight:700}

/* button */
.btn{position:absolute;display:flex;height:38px;font-size:12px;font-weight:700;color:#fff;letter-spacing:.3px}
.btn .label{background:var(--blue);display:flex;align-items:center;padding:0 16px}
.btn .chev{background:var(--arrow-seg);width:30px;display:flex;align-items:center;justify-content:center}
.btn.dark .label{background:#222}

/* header */
.header{top:0;height:79px;background:#fff}
.brand{position:absolute;left:174px;top:20px;display:flex;align-items:center;gap:9px}
.brand .dot{width:38px;height:38px;border-radius:50%;background:var(--blue)}
.brand span{font-size:24px;font-weight:700;color:var(--blue)}
.nav{position:absolute;top:34px;font-size:12px;font-weight:500;color:#333;letter-spacing:.2px}
.nav.active{color:var(--blue)}

/* hero */
.hero{top:79px;height:614px;clip-path:polygon(0 0,100% 0,100% 565px,0 100%)}
.hero .photo{position:absolute;inset:0;background:linear-gradient(180deg,#3d5f85 0%,#2c4870 45%,#2a3d55 75%,#3c4f63 100%)}
.hero .tint{position:absolute;inset:0;background:linear-gradient(90deg,rgba(20,60,120,.35),rgba(20,80,170,.45))}
.hero h1{position:absolute;top:195px;left:0;width:1200px;text-align:center;color:#fff;font-size:44px;line-height:47px;font-weight:700}
.dots{position:absolute;top:520px;left:512px;display:flex;gap:5px}
.dots i{width:42px;height:4px;background:#fff;display:block}
.dots i.off{background:rgba(255,255,255,.45)}

/* services */
.services{top:692px;height:678px;background:var(--grey-bg)}
.svc{position:absolute;top:116px;width:264px;height:444px;background:#fff;box-shadow:0 1px 4px rgba(0,0,0,.12);text-align:center}
.svc .pic{width:192px;height:192px;border-radius:50%;margin:28px auto 0}
.svc h3{margin-top:26px;font-size:19px;line-height:25px;font-weight:500;color:#3a3a3a}
.svc p{margin:16px auto 0;width:214px;font-size:13px;line-height:25px;color:var(--text)}

/* specializing */
.special{top:1370px;height:474px;background:#fff}
.spec{position:absolute;top:136px;width:270px;height:240px;background:#fff;box-shadow:0 1px 4px rgba(0,0,0,.14)}
.spec .pic{height:176px}
.spec h3{text-align:center;margin-top:21px;font-size:20px;font-weight:500;color:#3a3a3a}

/* about */
.about{top:1844px;height:494px}
.about .video{position:absolute;left:0;top:0;width:624px;height:494px;background:linear-gradient(160deg,#4a4a48 0%,#2d2c2a 55%,#3a3024 100%)}
.about .panel{position:absolute;left:624px;top:0;width:576px;height:494px;background:linear-gradient(135deg,#1a64bf,#0d4ea3)}
.about h2{position:absolute;left:49px;top:121px;font-size:29px;font-weight:700;color:#fff}
.about p{position:absolute;left:46px;top:170px;width:362px;font-size:13.5px;line-height:24.5px;color:#e9f0fb;text-align:justify}

/* team */
.team{top:2338px;height:528px;background:var(--grey-bg)}
.member{position:absolute;top:129px;width:195px;height:304px;background:#fff;box-shadow:0 1px 4px rgba(0,0,0,.12);text-align:center}
.member .pic{width:130px;height:130px;border-radius:50%;margin:16px auto 0}
.member h4{margin-top:16px;font-size:14px;font-weight:500;color:#222}
.member .role{font-size:13px;color:#999;margin-top:2px}
.member p{margin:12px auto 0;width:170px;font-size:11px;line-height:20px;color:var(--text)}

/* featured */
.featured{top:2866px;height:554px;background:#fff}

/* tips */
.tips{top:3420px;height:659px;background:var(--grey-bg)}
.tip{position:absolute;left:172px;width:857px;border-top:1px solid #d8d8d8}
.tip h4{position:absolute;left:0;font-size:17px;font-weight:500;color:var(--blue)}
.tip p{position:absolute;left:293px;width:572px;font-size:12.5px;line-height:23px;color:var(--text)}

/* cta */
.cta{top:4079px;height:227px;background:linear-gradient(90deg,#1559b0,#1a62bd)}
.cta h2{position:absolute;top:57px;left:0;width:1200px;text-align:center;color:#fff;font-size:24px;line-height:36px;font-weight:500}

/* footer */
.footer{top:4306px;height:302px;background:var(--footer);color:#ddd}
.footer .brand{left:172px;top:80px}
.footer .brand span{color:#fff;font-size:30px}
.footer .brand .dot{width:52px;height:52px;background:#fff}
.fcol{position:absolute;top:48px}
.fcol h5{font-size:17px;font-weight:500;color:#fff;margin-bottom:14px}
.fcol li{list-style:none;font-size:11.5px;line-height:24px;color:#ddd}
.rule{position:absolute;left:172px;top:224px;width:855px;height:3px;background:var(--blue)}
.social{position:absolute;left:172px;top:260px;display:flex;gap:14px}
.social i{display:block;width:18px;height:18px;border-radius:50%;background:#e6e6e6}
.copy{position:absolute;right:172px;top:266px;font-size:10.5px;color:#ccc}
</style>
</head>
<body>

<header class="section header">
  <div class="brand"><div class="dot"></div><span>BRACKWELL</span></div>
  <div class="nav active" style="left:419px">HOME</div>
  <div class="nav" style="left:488px">OUR SERVICES</div>
  <div class="nav" style="left:605px">MEET THE TEAM</div>
  <div class="nav" style="left:734px">CONTACT</div>
  <svg class="abs" style="left:831px;top:31px" width="18" height="18" viewBox="0 0 18 18" fill="none" stroke="#444" stroke-width="2"><circle cx="7.5" cy="7.5" r="5.5"/><path d="M11.5 11.5L16 16"/></svg>
  <div class="btn" style="left:889px;top:21px"><div class="label">REQUEST A QUOTE</div><div class="chev"><svg width="12" height="12" viewBox="0 0 12 12" fill="none" stroke="#ddd" stroke-width="1.4"><path d="M2 2l4 4-4 4M6 2l4 4-4 4"/></svg></div></div>
</header>

<section class="section hero">
  <div class="photo" role="img" aria-label="Modern two-storey house with large windows at dusk"></div>
  <div class="tint"></div>
  <h1>EXPERIENCE THE<br>BRACKWELL DIFFERENCE</h1>
  <div class="btn" style="left:511px;top:314px;height:36px"><div class="label">GET STARTED TODAY</div><div class="chev"><svg width="12" height="12" viewBox="0 0 12 12" fill="none" stroke="#ddd" stroke-width="1.4"><path d="M2 2l4 4-4 4M6 2l4 4-4 4"/></svg></div></div>
  <div class="dots"><i></i><i></i><i class="off"></i><i></i></div>
</section>

<section class="section services">
  <h2 class="title" style="top:41px">OUR <b>SERVICES</b></h2>
  <div class="svc" style="left:172px">
    <div class="pic" role="img" aria-label="Worker using a nail gun on roof shingles" style="background:radial-gradient(circle at 45% 40%,#8a8a82,#4e4f4c)"></div>
    <h3>EXTERIOR<br>RENOVATIONS</h3>
    <p>Looking for a reputable company to replace those aging shingles? Wanting to update the look of your home to add more curb appeal</p>
  </div>
  <div class="svc" style="left:467px">
    <div class="pic" role="img" aria-label="Builder installing ceiling panels in a garage" style="background:radial-gradient(circle at 50% 45%,#c9a684,#5a4a3e)"></div>
    <h3>DETACHED GARAGE<br>CONSTRUCTION</h3>
    <p>Looking for a reputable company to replace those aging shingles? Wanting to update the look of your home to add more curb appeal</p>
  </div>
  <div class="svc" style="left:762px">
    <div class="pic" role="img" aria-label="Sketch-style rendering of a new modern house" style="background:radial-gradient(circle at 50% 45%,#b9bcc0,#5f6468)"></div>
    <h3>NEW HOME<br>CONSTRUCTION</h3>
    <p>Looking for a reputable company to replace those aging shingles? Wanting to update the look of your home to add more curb appeal</p>
  </div>
</section>

<section class="section special">
  <h2 class="title" style="top:68px">WE <b>SPECIALIZING</b></h2>
  <div class="spec" style="left:172px"><div class="pic" role="img" aria-label="Installer drilling vinyl siding" style="background:linear-gradient(160deg,#d6d6d8,#7a6a5c)"></div><h3>Vinyl Siding</h3></div>
  <div class="spec" style="left:465px"><div class="pic" role="img" aria-label="House clad in board and batten siding" style="background:linear-gradient(160deg,#2e3c5c,#a7b6c9 60%,#7e8da0)"></div><h3>Corwin Maddox Siding</h3></div>
  <div class="spec" style="left:758px"><div class="pic" role="img" aria-label="Aluminum soffit and fascia under a roofline" style="background:linear-gradient(180deg,#a9c0dc,#c9bfa6 45%,#8a5a44)"></div><h3>Aluminum Soffit/fascia</h3></div>
</section>

<section class="section about">
  <div class="video" role="img" aria-label="Modern timber-clad house at twilight, video preview"></div>
  <svg class="abs" style="left:274px;top:244px" width="70" height="70" viewBox="0 0 70 70"><circle cx="35" cy="35" r="32" fill="rgba(0,0,0,.25)" stroke="#fff" stroke-width="3"/><path d="M28 22l20 13-20 13z" fill="#fff"/></svg>
  <div class="panel">
    <h2>ABOUT US</h2>
    <p>Lorem ipsum dolor sit amet, consectetur adipiscing elit, sed do eiusmod tempor incididunt ut labore et dolore magna aliqua. Ut enim ad minim veniam, quis nostrud exercitation ullamco laboris nisi ut aliquip ex ea commodo consequat. Duis aute irure dolor in reprehenderit in voluptate velit esse cillum dolore eu fugiat nulla pariatur. Excepteur sint occaecat cupidatat non proident, sunt in culpa qui officia deserunt mollit anim Lorem ipsum dolor sit amet, consectetur adipiscing elit, sed do eiusmod tempor.</p>
  </div>
</section>

<section class="section team">
  <h2 class="title" style="top:54px">THE <b>BRACKWELL</b> TEAM</h2>
  <svg class="abs" style="left:90px;top:232px" width="28" height="56" viewBox="0 0 28 56" fill="none" stroke="#aaa" stroke-width="1.5"><path d="M26 2L2 28l24 26"/></svg>
  <svg class="abs" style="left:1070px;top:232px" width="28" height="56" viewBox="0 0 28 56" fill="none" stroke="#aaa" stroke-width="1.5"><path d="M2 2l24 26L2 54"/></svg>
  <div class="member" style="left:173px"><div class="pic" role="img" aria-label="Portrait of the general manager" style="background:#7d8f6a"></div><h4>Dorian Welks</h4><div class="role">General Manager</div><p>He is principally focused on the building component of the company in addition to.</p></div>
  <div class="member" style="left:394px"><div class="pic" role="img" aria-label="Portrait of the operations manager" style="background:#8a9a70"></div><h4>Hollis Ambery</h4><div class="role">Operations Manager</div><p>He is principally focused on the building component of the company in addition to.</p></div>
  <div class="member" style="left:614px"><div class="pic" role="img" aria-label="Portrait of the field service manager" style="background:#7f9168"></div><h4>Caspar Lindqvar</h4><div class="role">Field Service Manager</div><p>He is principally focused on the building component of the company in addition to.</p></div>
  <div class="member" style="left:834px"><div class="pic" role="img" aria-label="Portrait of the site supervisor" style="background:#86956e"></div><h4>Rowan Telfair</h4><div class="role">Site Supervisor</div><p>He is principally focused on the building component of the company in addition to.</p></div>
</section>

<section class="section featured">
  <h2 class="title" style="top:48px">FEATURED <b>WORK</b></h2>
  <div class="abs" role="img" aria-label="Completed modern wood-sided home lit at dusk" style="left:172px;top:120px;width:517px;height:350px;background:linear-gradient(180deg,#4d5f7e 0%,#8a7f86 40%,#5a4630 75%,#3d3a28 100%)"></div>
  <div class="abs" role="img" aria-label="House under construction with stone and wood exterior" style="left:710px;top:120px;width:317px;height:168px;background:linear-gradient(180deg,#c9c7c2,#5a4c40 60%,#7a6a58)"></div>
  <div class="abs" role="img" aria-label="Dark-sided house roofline covered in snow" style="left:710px;top:302px;width:317px;height:168px;background:linear-gradient(180deg,#e3e5e8,#4b4848 45%,#7a4a38 80%,#2f2f33)"></div>
</section>

<section class="section tips">
  <h2 class="title" style="top:50px">HELPFUL <b>EXTERIOR TIPS</b></h2>
  <div class="tip" style="top:133px;height:113px"><h4 style="top:30px">Nequporroui suamstuio?</h4><p style="top:24px">Lorem ipsum dolor sit amet, consectetur adipiscing elit, sed do eiusmod tempor incididunt ut labore et dolore magna aliqua. Ut enim ad minim veniam, quis nostrud exercitation ullamco laboris nisi ut aliquip ex ea commodo consequat. Duis aute irure dolor in reprehenderit in volupt</p></div>
  <div class="tip" style="top:246px;height:78px"><h4 style="top:28px">Lorwem usouporrsuamstuio?</h4><p style="top:22px">Lorem ipsum dolor sit amet, consectetur adipiscing elit, sed do eiusmod tempor incididunt ut labore et dolore magna aliqua. Ut enim ad minim veniam, quis nostrud exercitation ullamc.</p></div>
  <div class="tip" style="top:324px;height:82px"><h4 style="top:28px">Lorwerrsuamstuio?</h4><p style="top:22px">Lorem ipsum dolor sit amet, consectetur adipiscing elit, sed do eiusmod tempor incididunt ut labore et dolore magna aliqua. Ut enim ad minim veniam, quis nostrud exercitation ullamc.</p></div>
  <div class="tip" style="top:406px;height:84px"><h4 style="top:28px">Lorwem usoupomstuio?</h4><p style="top:22px">Lorem ipsum dolor sit amet, consectetur adipiscing elit, sed do eiusmod tempor incididunt ut labore et dolore magna aliqua. Ut enim ad minim veniam, quis nostrud exercitation ullamc.</p></div>
  <div class="tip" style="top:490px;height:140px;border-top:1px solid #d8d8d8"><h4 style="top:28px">Lorwem usouporrsuamstuio?</h4><p style="top:22px">Lorem ipsum dolor sit amet, consectetur adipiscing elit, sed do eiusmod tempor incididunt ut labore et dolore magna aliqua. Ut enim ad minim veniam, quis nostrud exercitation ullamc.orem ipsum dolor sit amet, consectetur adipiscing elit, sed do eiusmod tempor incididunt ut labore et dolore magna aliqua. Ut enim ad minim veniam, quis nostrud exercitation ullamc.</p></div>
</section>

<section class="section cta">
  <h2>Honest and reliable construction service in Calderwood and area.<br>We take pride in each and every project</h2>
  <div class="btn dark" style="left:517px;top:147px;height:38px"><div class="label">REQUEST A QUOTE</div><div class="chev"><svg width="12" height="12" viewBox="0 0 12 12" fill="none" stroke="#ddd" stroke-width="1.4"><path d="M2 2l4 4-4 4M6 2l4 4-4 4"/></svg></div></div>
</section>

<footer class="section footer">
  <div class="brand"><div class="dot"></div><span>BRACKWELL</span></div>
  <div class="fcol" style="left:435px"><h5>Contact</h5><ul><li>Ashford Park, Alberta</li><li>Email:info@brackwellfabricators.ca</li><li>Phone:555-014-2286</li></ul></div>
  <div class="fcol" style="left:660px"><h5>Office Hours</h5><ul><li>Mon-Fri: 8:00-4:30</li><li>Sat-Sun &amp; Holidays: Closed</li></ul></div>
  <div class="fcol" style="left:893px"><h5>Links</h5><ul><li>Home</li><li>Our Services</li><li>Meet the Team</li></ul></div>
  <div class="btn" style="left:896px;top:188px;height:36px"><div class="label" style="padding:0 14px">QUICK CHAT</div><div class="chev"><svg width="12" height="12" viewBox="0 0 12 12" fill="none" stroke="#ddd" stroke-width="1.4"><path d="M2 2l4 4-4 4M6 2l4 4-4 4"/></svg></div></div>
  <div class="rule"></div>
  <div class="social" aria-label="Social links"><i></i><i></i><i></i><i></i><i></i></div>
  <div class="copy">Copyright 2020 Brackwell Builders. All Rights Reserved</div>
</footer>

</body>
</html>
```